New Carpathian Table Billboard

Need to prepare a billboard for a KOSHER supermarket that is under new ownership. The billboard needs to have a good catch phrase such as:

A NEW Fresh KOSHER Grocery Experience Has Arrived!

The Legacy Continues...
Stop In To See The NEW Carpathian Table Foods!

Kosher Grocery Shopping at it's Finest!
Come See The NEW & IMPROVED Carpathian Table Foods

No Pictures. Choose various color backgrounds and send me proofs. Think of other catchy phrases and provide examples. Don't only use the phrases I gave above.

The store was taken under new ownership and we want to promote the NEW and Improved Store.

Target Market(s)

Orthodox Jewish

Industry/Entity Type

Grocery Store

Requirements
Must have
• Logo
• Linwell & Harbury in Skokie
Nice to have
• No Pictures.
Should not have
• Too much wording.

```html
<!DOCTYPE html>
<html lang="en">
<head>
<meta charset="utf-8">
<title>Carpathian Table Foods Billboard</title>
<link href="https://fonts.googleapis.com/css2?family=Alfa+Slab+One&display=swap" rel="stylesheet">
<style>
  :root {
    --page-bg: #e6e9f0;
    --board-blue: #0a0a9c;
    --accent-red: #f01414;
    --panel-white: #ffffff;
    --text-white: #ffffff;
  }
  * { margin: 0; padding: 0; box-sizing: border-box; }
  html, body {
    width: 1200px;
    height: 720px;
    overflow: hidden;
    background: var(--page-bg);
  }
  .billboard {
    position: absolute;
    left: 30px;
    top: 308px;
    width: 1140px;
    height: 102px;
    background: var(--board-blue);
    box-shadow: 0 3px 6px rgba(0,0,0,0.35);
    font-family: "Alfa Slab One", "Rockwell", serif;
    color: var(--text-white);
    overflow: hidden;
  }
  .brand-panel {
    position: absolute;
    left: 0;
    top: 0;
    width: 240px;
    height: 102px;
  }
  .brand-name {
    position: absolute;
    left: 58px;
    top: 18px;
    width: 150px;
    height: 66px;
    display: flex;
    align-items: center;
    justify-content: center;
    text-align: center;
    font-size: 17px;
    line-height: 1.1;
    color: var(--board-blue);
  }
  .headline {
    position: absolute;
    left: 280px;
    top: 10px;
    font-size: 31px;
    line-height: 1.2;
    letter-spacing: 0.5px;
    white-space: nowrap;
  }
  .headline-strong {
    display: block;
    font-size: 43px;
    line-height: 1;
    letter-spacing: 1px;
  }
  .location-tag {
    position: absolute;
    left: 794px;
    top: 59px;
    width: 346px;
    height: 27px;
    background: var(--accent-red);
    clip-path: polygon(10px 0, 100% 0, 100% 100%, 0 100%);
    font-size: 14px;
    line-height: 27px;
    padding-left: 30px;
    letter-spacing: 0.4px;
    white-space: nowrap;
  }
</style>
</head>
<body>
  <div class="billboard">
    <svg class="brand-panel" viewBox="0 0 240 102" aria-hidden="true">
      <polygon points="48,0 222,0 229,102 40,102" fill="var(--panel-white)"/>
      <polygon points="36,0 72,0 48,58" fill="var(--accent-red)"/>
      <polygon points="212,102 229,102 240,102 220,58" fill="var(--accent-red)"/>
    </svg>
    <div class="brand-name">Carpathian Table Foods</div>

    <h1 class="headline">
      A NEW Fresh KOSHER Grocery Experience
      <span class="headline-strong">HAS ARRIVED!</span>
    </h1>

    <div class="location-tag">Linwell &amp; Harbury in Skokie</div>
  </div>
</body>
</html>
```